Bespoke Builders Business Card Design

We need a business card for an established builder of high quality bespoke homes in Auckland and Northland. We build and renovate homes collaboratively facilitating effective communication between owners, builders, architects, suppliers and tradespeople. We have never built or renovated a home that leaks or has faults. We only use reliable materials. We have never been sued or had legal action taken against us. We are honest builders of bespoke homes not group mass produced homes. Our niche market is in character homes. We practice sustainability and have built a lot of coastal property. We have been in business for over thirty years . We would like to see natural colors of the environment sand,sea and maybe vegetation . The design should communicate quality, sustainability,fair pricing, open communication and the originality of bespoke building. And the fact that the builder is registered.

Industry/Entity Type

Business

Contact Information for Business Card

Rowan Tellick Builders
Ph. 021583917
18 Kestrel Rd Harwood Bay Auckland 0814
PO Box 927 Mangawhai 0583

```html
<!DOCTYPE html>
<html lang="en">
<head>
<meta charset="utf-8">
<title>Rowan Tellick Builders – Business Card</title>
<link rel="stylesheet" href="https://fonts.googleapis.com/css2?family=Playfair+Display:wght@700&family=Open+Sans:wght@400&display=swap">
<style>
  :root {
    --canvas: #e9e6e1;
    --paper: #ffffff;
    --maroon: #5a1a1c;
    --maroon-deep: #3d0f10;
    --ink: #111111;
    --gloss-black: #0c0c0c;
    --card-text-light: #f4f1ee;
  }
  html, body {
    margin: 0;
    padding: 0;
    width: 1200px;
    height: 892px;
    overflow: hidden;
    background: var(--canvas);
  }
  .canvas {
    position: relative;
    width: 1200px;
    height: 892px;
  }
  .card {
    position: absolute;
    top: 291px;
    width: 540px;
    height: 309px;
    overflow: hidden;
    box-shadow: 0 6px 18px rgba(0,0,0,0.25);
  }
  .card--front { left: 50px; background: var(--paper); }
  .card--back  { left: 610px; background: linear-gradient(160deg, #1c1c1c 0%, var(--gloss-black) 60%); }
  .card__art {
    position: absolute;
    inset: 0;
  }
  .card__name {
    position: absolute;
    margin: 0;
    font-family: "Playfair Display", "Times New Roman", serif;
    font-weight: 700;
    white-space: nowrap;
  }
  .card--front .card__name {
    top: 38px;
    left: 0;
    width: 540px;
    text-align: center;
    font-size: 38px;
    color: var(--ink);
  }
  .card--back .card__name {
    top: 128px;
    left: 36px;
    font-size: 38px;
    letter-spacing: 1px;
    color: var(--card-text-light);
  }
  .card__contact {
    position: absolute;
    top: 170px;
    left: 0;
    width: 540px;
    text-align: center;
    font-family: "Open Sans", Arial, sans-serif;
    font-size: 18px;
    line-height: 27px;
    color: var(--card-text-light);
  }
  .card__contact p { margin: 0; }
  .card__phone { margin-bottom: 6px !important; }
</style>
</head>
<body>
<main class="canvas">
  <section class="card card--front" aria-label="Business card front">
    <svg class="card__art" viewBox="0 0 540 309" width="540" height="309" aria-hidden="true">
      <defs>
        <linearGradient id="maroonFill" x1="0" y1="0" x2="1" y2="1">
          <stop offset="0" stop-color="#6e2a2b"/>
          <stop offset="0.45" stop-color="#561718"/>
          <stop offset="1" stop-color="#3d0f10"/>
        </linearGradient>
      </defs>
      <path d="M0 100 L26 142 L498 142 L540 166 L540 309 L0 309 Z" fill="url(#maroonFill)"/>
      <path d="M12 106 L32 134 L496 134 L524 150" fill="none" stroke="#111" stroke-width="4" stroke-linejoin="miter"/>
    </svg>
    <h1 class="card__name">Rowan Tellick Builders</h1>
    <div class="card__contact">
      <p class="card__phone">021583917</p>
      <p>18 Kestrel Rd Harwood Bay Auckland 0814</p>
      <p>PO Box 927 Mangawhai 0583</p>
    </div>
  </section>

  <section class="card card--back" aria-label="Business card back">
    <h2 class="card__name">Rowan Tellick Builders</h2>
  </section>
</main>
</body>
</html>
```